Moxy Fen needs some awesome stationary

Do you have what it takes to get my brand? You either do or you don't, have a crack at a design and you my just win my business.

I don't want to waste your or my time, so put your creative genius on either a business card or envelope.

I however need a package of stationary that follows the same brand. I will message you to complete the remaining should I like your first submission.

Here is what I need, have a go!

Basically I need the following for my small business based in melbourne.
- Letterhead (printer ready and MS Word)
- Business Card
- Compliments Slip
- Envelope
- Proposal Cover Page (MS Word only)
- Presentation Folder
- Marbled Fox Cards
- Student Name Tent
- Index Cards
- Vell-Ka

I am establishing the brand and it must be modern, professional but also relaxed; that is not formal and not corporate. It represents a company are leaders, but small enough to care and operate like a bunch of friends. We are bringing people and conversations back to business, and turfing out all the bureaucracy and crazy and wasteful procedures. Its about "lets talk and figure it out together and find even better ways".

Target Market(s)

Mainly companies that build software products, but Agile practices are used in many other industries (even graphic design projects)

Industry/Entity Type

Information Technology

Font styles to use
Sans Serif

Colors
3176b5
aaaaaa

Requirements
Must have
• I like curves and circles and not boxes or rectangles.
• I want a colour rich design with my brand colours, but it must be balanced.
• I want more modern than traditional, but simple modern
Should not have
• Not corporate
• Please don't waste my time if your not going to think about it.
• Don't mess with my primary logo
• Don't change my colours
• Don't overlay logo on image

```html
<!DOCTYPE html>
<html lang="en">
<head>
<meta charset="utf-8">
<title>Moxy Fen – Business Card</title>
<link rel="stylesheet" href="https://fonts.googleapis.com/css2?family=Montserrat:wght@600&family=Open+Sans:wght@600&family=PT+Sans+Narrow&display=swap">
<style>
  :root {
    --brand-blue: #3176b5;
    --deep-blue: #1d56a3;
    --stripe-blue: #2a66b0;
    --brand-grey: #aaaaaa;
    --paper: #ffffff;
    --backdrop: #eceff3;
  }
  * { margin: 0; padding: 0; box-sizing: border-box; }
  html, body { width: 1200px; height: 800px; overflow: hidden; }
  body {
    background: var(--backdrop);
    display: flex; align-items: center; justify-content: center; gap: 40px;
    font-family: "Open Sans", sans-serif;
  }
  .card {
    position: relative; width: 540px; height: 309px; overflow: hidden;
    border-radius: 4px; box-shadow: 0 6px 18px rgba(0,0,0,.15);
  }

  /* Front */
  .card-front {
    background: linear-gradient(180deg, var(--deep-blue) 0%, var(--deep-blue) 38%, var(--stripe-blue) 38%, var(--stripe-blue) 62%, var(--deep-blue) 62%, var(--brand-blue) 100%);
    display: flex; flex-direction: column; align-items: center; justify-content: center; gap: 18px;
  }
  .brand-mark { width: 74px; height: 74px; border-radius: 50%; background: var(--paper); }
  .brand-name { font-family: "Open Sans", sans-serif; font-weight: 600; color: var(--paper); font-size: 30px; letter-spacing: .5px; }

  /* Back */
  .card-back { background: var(--deep-blue); }
  .band-white-top { position: absolute; left: 0; top: 0; width: 100%; height: 34px; background: var(--paper); }
  .band-brand { position: absolute; left: 0; top: 34px; width: 100%; height: 78px; background: linear-gradient(90deg, var(--deep-blue), var(--brand-blue)); display: flex; align-items: center; justify-content: flex-end; gap: 14px; padding-right: 34px; }
  .band-brand .brand-mark { width: 46px; height: 46px; background: var(--brand-grey); }
  .band-brand .brand-name { font-size: 28px; }
  .band-white-mid { position: absolute; left: 0; top: 112px; width: 100%; height: 30px; background: var(--paper); }
  .person { position: absolute; left: 28px; top: 168px; color: var(--paper); }
  .person-name { font-family: "Montserrat", sans-serif; font-weight: 600; font-size: 15px; letter-spacing: 1.5px; text-transform: uppercase; }
  .person-role { font-family: "PT Sans Narrow", sans-serif; font-size: 12px; margin-top: 3px; }
  .divider { position: absolute; left: 246px; top: 142px; width: 18px; height: 167px; background: linear-gradient(180deg, #174a8f, var(--deep-blue)); }
  .contacts { position: absolute; left: 250px; top: 158px; list-style: none; color: var(--paper); font-family: "PT Sans Narrow", sans-serif; font-size: 13px; }
  .contacts li { display: flex; align-items: center; gap: 12px; height: 22px; }
  .contacts svg { width: 11px; height: 11px; fill: var(--paper); flex: none; }
</style>
</head>
<body>
  <section class="card card-front" aria-label="Business card front">
    <div class="brand-mark"></div>
    <div class="brand-name">Moxy Fen</div>
  </section>

  <section class="card card-back" aria-label="Business card back">
    <div class="band-white-top"></div>
    <div class="band-brand">
      <div class="brand-mark"></div>
      <div class="brand-name">Moxy Fen</div>
    </div>
    <div class="band-white-mid"></div>
    <div class="person">
      <div class="person-name">Dane Halloway</div>
      <div class="person-role">CEO, Professional Scrum Trainer</div>
    </div>
    <div class="divider"></div>
    <ul class="contacts">
      <li><svg viewBox="0 0 12 12"><path d="M6 0a4 4 0 0 0-4 4c0 3 4 8 4 8s4-5 4-8a4 4 0 0 0-4-4zm0 5.5A1.5 1.5 0 1 1 6 2.5a1.5 1.5 0 0 1 0 3z"/></svg>PO Box 4417, Larkfield North, VIC 3199, Australia</li>
      <li><svg viewBox="0 0 12 12"><path d="M1 3c0-1 1-2 2-2h6c1 0 2 1 2 2v1H8V3H4v1H1zm1 2h8l1 6H1z"/></svg>1300MOXYFN</li>
      <li><svg viewBox="0 0 12 12"><rect x="3" y="0" width="6" height="12" rx="1"/></svg>+61 400 372 618</li>
      <li><svg viewBox="0 0 12 12"><path d="M0 2h12v8H0zm1 1 5 4 5-4"/></svg>dane@moxyfen.com.au</li>
      <li><svg viewBox="0 0 12 12"><path d="M6 0a6 6 0 1 0 0 12A6 6 0 0 0 6 0zm0 1.2c.8 1 1.3 2.5 1.4 4.2H4.6C4.7 3.7 5.2 2.2 6 1.2zM4.6 6.6h2.8c-.1 1.7-.6 3.2-1.4 4.2-.8-1-1.3-2.5-1.4-4.2z"/></svg>www.moxyfen.com.au</li>
    </ul>
  </section>
</body>
</html>
```